Aquavelo- plumbing service flyer

Hello,
We would like to create flyer for our plumbing company Aquavelo
- we have 2 web domains
aquavelo-example.hr ( official)
preuredjenjedoma-example.hr ( for bathroom renovation)

- we would like to create a similar Z-fold flyer ( from A4 paper) for our services
- We are sending images used on our websites. Of Course, it is allowed to put some of their own. Depending on design
- sending word with text which should go on each page. Text can be modified but in the sense of a page. The massage on a page should be as in word.
What is important to us:
- to stay in blue color
- It should be 1 page when fully open. So it looks like the complete page of information
- first/front page should be with our logo and phone number. more focus on emergency plumbing.
- back page should be about bathroom remodeling. Not necessary but would be received more points
- please don't use images of regular plumbers from Pixelvault and similar. we don't want to use this stock's regular images as all others.

Target Market(s)

Bathroom remodeling and emergency plumbing

Industry/Entity Type

Construction-Plumbing

Colors
0054AA
0677BA
7BADD7
CADEEF
E8F1F8

Requirements
Must have
• Logo

```html
<!DOCTYPE html>
<html lang="en">
<head>
<meta charset="utf-8">
<title>Aquavelo – Plumbing Service Flyer</title>
<link href="https://fonts.googleapis.com/css2?family=Anton&family=Teko:wght@400;500;600&family=Poppins:ital,wght@1,400&display=swap" rel="stylesheet">
<style>
  :root {
    --stage: #fdb813;
    --navy: #1a2c6b;
    --navy-deep: #14235a;
    --navy-mid: #223a85;
    --blue: #0054aa;
    --blue-bright: #0677ba;
    --sky: #7badd7;
    --yellow: #f9b214;
    --red: #e31e26;
    --white: #ffffff;
    --ink: #1b2f6e;
  }
  * { margin: 0; padding: 0; box-sizing: border-box; }
  html, body { width: 1200px; height: 2242px; overflow: hidden; background: var(--stage); }
  .canvas { position: relative; width: 1200px; height: 2242px; }

  .spread {
    position: absolute; left: 174px; width: 985px; height: 695px;
    transform: scale(0.869); transform-origin: top left;
    background: linear-gradient(160deg, #203a88 0%, var(--navy) 45%, var(--navy-deep) 100%);
    overflow: hidden;
    box-shadow: 0 22px 22px -12px rgba(120, 70, 0, .45);
  }
  .spread--inside { top: 850px; }
  .spread--outside { top: 1556px; }

  .backdrop { position: absolute; inset: 0; background: radial-gradient(ellipse at 70% 20%, rgba(123,173,215,.18), transparent 60%), radial-gradient(ellipse at 80% 85%, rgba(6,119,186,.2), transparent 55%); }

  .logo { position: absolute; display: flex; flex-direction: column; align-items: center; justify-content: center; gap: 8px; }
  .logo__disc { width: 160px; height: 160px; border-radius: 50%; background: radial-gradient(circle at 50% 40%, var(--blue-bright), var(--blue)); border: 6px solid var(--yellow); }
  .logo__name { font-family: "Anton", sans-serif; font-size: 46px; color: var(--white); letter-spacing: 1px; line-height: 1; }

  .swoosh { position: absolute; left: 0; top: 0; width: 985px; height: 695px; pointer-events: none; }

  .tagline { position: absolute; left: 24px; width: 275px; text-align: center; font-family: "Anton", sans-serif; color: var(--yellow); font-size: 29px; line-height: 40px; }
  .brandline { position: absolute; left: 24px; width: 275px; text-align: center; font-family: "Anton", sans-serif; color: var(--white); font-size: 54px; line-height: 1; }

  .contact-box { position: absolute; left: 24px; width: 275px; display: flex; align-items: center; gap: 14px; padding-left: 16px; }
  .contact-box--quick { top: 470px; height: 88px; background: #1f3a8c; }
  .contact-box--emergency { top: 572px; height: 88px; background: var(--red); }
  .contact-box__label { font-family: "Teko", sans-serif; font-weight: 400; color: var(--white); font-size: 24px; letter-spacing: 3px; line-height: 1; }
  .contact-box__sub { font-family: "Teko", sans-serif; color: var(--yellow); font-size: 19px; letter-spacing: 1px; line-height: 1.1; }
  .contact-box__phone { font-family: "Teko", sans-serif; font-weight: 500; color: var(--white); font-size: 40px; line-height: .9; letter-spacing: 1px; }
  .contact-box--emergency .contact-box__label { font-size: 17px; }

  .service { position: absolute; left: 372px; width: 540px; }
  .service__head { position: relative; height: 69px; background: var(--yellow); border-radius: 7px; display: flex; align-items: center; padding-left: 13px; }
  .service__title { font-family: "Anton", sans-serif; font-size: 54px; color: var(--ink); letter-spacing: .5px; line-height: 1; }
  .service__badge { position: absolute; right: 24px; top: -14px; width: 68px; height: 68px; border-radius: 50%; background: radial-gradient(circle, var(--sky), var(--blue-bright)); border: 2px solid var(--white); }
  .service__body { margin-top: 7px; height: 99px; border: 1.5px solid var(--yellow); border-radius: 10px; background: rgba(20, 35, 90, .55); padding: 7px 12px; font-family: "Poppins", sans-serif; font-style: italic; font-size: 9.4px; line-height: 13.6px; color: var(--white); text-align: justify; overflow: hidden; }

  .fold { position: absolute; top: 0; bottom: 0; width: 1px; background: rgba(255,255,255,.06); }

  .heading { position: absolute; font-family: "Anton", sans-serif; line-height: 1; }
  .heading--yellow { color: var(--yellow); }
  .heading--white { color: var(--white); }

  .copy { position: absolute; font-family: "Poppins", sans-serif; font-style: italic; font-size: 9.4px; line-height: 13.5px; color: var(--white); text-align: justify; }

  .phone-line { position: absolute; left: 25px; top: 606px; display: flex; align-items: center; gap: 12px; }
  .phone-line__label { font-family: "Teko", sans-serif; color: var(--white); font-size: 20px; letter-spacing: 3px; line-height: 1; }
  .phone-line__number { font-family: "Teko", sans-serif; font-weight: 500; color: var(--white); font-size: 46px; line-height: .9; letter-spacing: 1px; }

  .feature-row { position: absolute; left: 682px; width: 278px; height: 62px; border: 1.5px solid var(--yellow); border-radius: 10px; background: rgba(34, 58, 133, .5); }
  .feature { position: absolute; width: 140px; text-align: center; }
  .feature__circle { width: 100px; height: 100px; margin: 0 auto; border-radius: 50%; border: 1.5px solid var(--yellow); background: var(--navy-mid); display: flex; align-items: center; justify-content: center; }
  .feature__label { margin-top: 8px; font-family: "Anton", sans-serif; font-size: 12px; color: var(--white); letter-spacing: .3px; }
  .feature__cta { font-family: "Anton", sans-serif; color: var(--white); font-size: 12px; line-height: 11px; }
</style>
</head>
<body>
<main class="canvas">

  <section class="spread spread--inside">
    <div class="backdrop" role="img" aria-label="Soft blue backdrop of a plumber at work"></div>
    <div class="fold" style="left:328px"></div>
    <div class="fold" style="left:658px"></div>

    <svg class="swoosh" viewBox="0 0 985 695" aria-hidden="true">
      <path d="M0 200 Q 150 222 372 236" stroke="#f9b214" stroke-width="4" fill="none"/>
      <path d="M912 196 L985 182" stroke="#f9b214" stroke-width="2" fill="none"/>
    </svg>

    <div class="logo" style="left:47px; top:45px; width:225px; height:240px;">
      <div class="logo__disc"></div>
      <div class="logo__name">AQUAVELO</div>
    </div>

    <p class="tagline" style="top:300px">USING TECH TO<br>FACILITATE YOUR LIFE.</p>
    <p class="brandline" style="top:384px">AQUAVELO</p>

    <div class="contact-box contact-box--quick">
      <svg width="56" height="40" viewBox="0 0 56 40" aria-hidden="true">
        <rect x="14" y="4" width="40" height="32" fill="none" stroke="#fff" stroke-width="2.5"/>
        <path d="M14 4 L34 22 L54 4 M14 36 L29 20 M54 36 L39 20" fill="none" stroke="#fff" stroke-width="2"/>
        <path d="M2 12 H10 M0 20 H10 M4 28 H10" stroke="#fff" stroke-width="2"/>
      </svg>
      <div>
        <p class="contact-box__label">QUICK CONTACT</p>
        <p class="contact-box__sub">LEACKAGE / CLOGGED?</p>
      </div>
    </div>

    <div class="contact-box contact-box--emergency">
      <svg width="44" height="50" viewBox="0 0 44 50" aria-hidden="true">
        <rect x="3" y="6" width="24" height="40" rx="4" fill="none" stroke="#fff" stroke-width="2.5"/>
        <path d="M10 20 q-2 8 6 14 l3 -3 -3 -4 -2 1 q-3 -3 -2 -6 l2 -1 -1 -4z" fill="#fff"/>
        <circle cx="32" cy="12" r="10" fill="#e31e26" stroke="#fff" stroke-width="2"/>
        <text x="32" y="16" text-anchor="middle" font-family="Teko, sans-serif" font-size="12" fill="#fff">24</text>
      </svg>
      <div>
        <p class="contact-box__label">EMERGENCY PLUMBING</p>
        <p class="contact-box__phone">091-555-0147</p>
      </div>
    </div>

    <article class="service" style="top:67px">
      <div class="service__head">
        <h2 class="service__title">PLUMBING SERVICE</h2>
        <div class="service__badge" role="img" aria-label="Round mascot badge"></div>
      </div>
      <p class="service__body">Our licensed team handles leaks, burst pipes, taps, boilers and water heaters in homes and offices across the city. We arrive on time, explain each step in plain words and agree a fair fixed price before any work begins, so there are never hidden costs. Every repair is tested twice and backed by a written guarantee. From a single dripping tap to a full pipe replacement, we bring the right parts in the van and leave your home clean and dry when the job is done.</p>
    </article>

    <article class="service" style="top:276px">
      <div class="service__head">
        <h2 class="service__title">DRAIN CLEANING</h2>
        <div class="service__badge" role="img" aria-label="Round mascot badge"></div>
      </div>
      <p class="service__body">Slow sinks, blocked toilets and smelly drains are cleared fast with high pressure jetting and a camera inspection of the whole line. We find the real cause of the blockage, not just the symptom, and remove it for good. Tree roots, grease and old scale are no match for our equipment. After every visit you get a short report with photos of your pipes. Regular maintenance plans keep water flowing freely all year long and protect your home from costly flooding and damage.</p>
    </article>

    <article class="service" style="top:485px">
      <div class="service__head">
        <h2 class="service__title">SPLASH POINTS</h2>
        <div class="service__badge" role="img" aria-label="Round flying mascot badge"></div>
      </div>
      <p class="service__body">Every job you book earns points in our loyalty program. Collect them with each repair, cleaning or installation and swap them for real discounts on future visits. Recommend us to friends and neighbours and we add bonus points to your account when they book their first service with our team. Members also get priority scheduling in busy seasons, a yearly free check of the water system and special offers on bathroom renovation projects planned with our partners.</p>
    </article>
  </section>

  <section class="spread spread--outside">
    <div class="backdrop" role="img" aria-label="Soft blue backdrop of smiling plumbers and a flying mascot"></div>
    <svg class="swoosh" viewBox="0 0 985 695" aria-hidden="true">
      <path d="M270 0 H985 V168 Q 640 212 270 212 Z" fill="#223d8e"/>
      <path d="M0 160 Q 120 176 250 196" stroke="#f9b214" stroke-width="4" fill="none"/>
      <path d="M250 210 Q 640 222 985 168" stroke="#f9b214" stroke-width="4" fill="none"/>
    </svg>
    <div class="fold" style="left:328px"></div>
    <div class="fold" style="left:658px"></div>

    <div class="logo" style="left:45px; top:40px; width:235px; height:250px;">
      <div class="logo__disc"></div>
      <div class="logo__name">AQUAVELO</div>
    </div>

    <h2 class="heading heading--yellow" style="left:25px; top:338px; font-size:31px; line-height:32px;">COUNT ON US<br>FOR PLUMBING</h2>
    <p class="copy" style="left:25px; top:410px; width:273px;">From a dripping tap to a complete bathroom renovation, our plumbers bring the right tools, spare parts and know-how to every home. Quick response, honest advice and tidy work are the standard we keep on every single visit. We plan each project with you, respect your time and budget, and stay available long after the job is finished.</p>

    <div class="phone-line">
      <svg width="46" height="50" viewBox="0 0 44 50" aria-hidden="true">
        <rect x="3" y="6" width="24" height="40" rx="4" fill="none" stroke="#fff" stroke-width="2.5"/>
        <path d="M10 20 q-2 8 6 14 l3 -3 -3 -4 -2 1 q-3 -3 -2 -6 l2 -1 -1 -4z" fill="#fff"/>
        <circle cx="32" cy="12" r="10" fill="#1a2c6b" stroke="#fff" stroke-width="2"/>
        <text x="32" y="16" text-anchor="middle" font-family="Teko, sans-serif" font-size="12" fill="#fff">24</text>
      </svg>
      <div>
        <p class="phone-line__label">EMERGENCY PLUMBING</p>
        <p class="phone-line__number">091-555-0147</p>
      </div>
    </div>

    <h2 class="heading heading--yellow" style="left:362px; top:38px; font-size:58px; letter-spacing:1px;">SPLASH</h2>
    <h2 class="heading heading--white" style="left:362px; top:100px; font-size:58px; letter-spacing:1px;">POINTS</h2>

    <h2 class="heading heading--yellow" style="left:685px; top:40px; font-size:46px;">COUNT ON US</h2>
    <h2 class="heading heading--white" style="left:685px; top:94px; font-size:46px;">FOR PLUMBING</h2>

    <p class="copy" style="left:362px; top:240px; width:262px;">Loyal customers deserve more. With Splash Points every booked service adds points to your personal account, and those points turn into real savings on repairs, maintenance and new installations. The more you book, the faster your balance grows. Members also get priority scheduling during busy seasons, a yearly free inspection of their water system and early access to seasonal offers. Points can be shared with family members living at the same address and used for any service we offer.</p>
    <p class="copy" style="left:362px; top:420px; width:262px;">Ask our team how to join on your next visit. Membership is free, points never expire and your first booking already earns a welcome bonus.</p>

    <div class="feature-row" style="top:254px"></div>
    <div class="feature-row" style="top:396px"></div>
    <div class="feature-row" style="top:539px"></div>

    <div class="feature" style="left:680px; top:235px">
      <div class="feature__circle">
        <svg width="56" height="44" viewBox="0 0 56 44" aria-hidden="true"><path d="M20 8 V4 H36 V8" stroke="#fff" stroke-width="4" fill="none"/><rect x="2" y="10" width="52" height="32" rx="5" fill="#fff"/><rect x="2" y="22" width="52" height="3" fill="#223a85"/><rect x="24" y="19" width="8" height="9" fill="#fff" stroke="#223a85" stroke-width="2"/></svg>
      </div>
      <p class="feature__label">REPAIRS</p>
    </div>
    <div class="feature" style="left:820px; top:235px">
      <div class="feature__circle">
        <svg width="60" height="60" viewBox="0 0 60 60" aria-hidden="true" fill="#fff">
          <circle cx="22" cy="22" r="13"/><circle cx="22" cy="22" r="5" fill="#223a85"/>
          <g stroke="#fff" stroke-width="6"><path d="M22 4 V40 M4 22 H40 M9 9 L35 35 M35 9 L9 35"/></g>
          <circle cx="42" cy="42" r="9"/><circle cx="42" cy="42" r="3.5" fill="#223a85"/>
          <g stroke="#fff" stroke-width="4"><path d="M42 30 V54 M30 42 H54 M33 33 L51 51 M51 33 L33 51"/></g>
        </svg>
      </div>
      <p class="feature__label">REPLACEMENTS</p>
    </div>
    <div class="feature" style="left:680px; top:377px">
      <div class="feature__circle"><p class="feature__cta">CONTACT OUR<br>EXPERTS NOW</p></div>
      <p class="feature__label">CONTACT</p>
    </div>
    <div class="feature" style="left:820px; top:377px">
      <div class="feature__circle">
        <svg width="50" height="56" viewBox="0 0 50 56" aria-hidden="true" fill="#fff">
          <path d="M8 22 a14 14 0 0 1 28 0 z"/><rect x="6" y="22" width="32" height="4"/>
          <rect x="4" y="36" width="36" height="20" rx="6"/>
          <path d="M42 4 a6 6 0 1 0 4 0 v8 h-4z M42 14 h4 v34 a2 2 0 0 1 -4 0z"/>
        </svg>
      </div>
      <p class="feature__label">MAINTENANCE</p>
    </div>
    <div class="feature" style="left:680px; top:520px">
      <div class="feature__circle">
        <svg width="70" height="70" viewBox="0 0 70 70" aria-hidden="true">
          <path d="M12 30 A24 24 0 0 1 58 30" stroke="#fff" stroke-width="3" fill="none"/>
          <path d="M58 40 A24 24 0 0 1 12 40" stroke="#fff" stroke-width="3" fill="none"/>
          <path d="M52 26 L58 32 L63 25" stroke="#fff" stroke-width="3" fill="none"/>
          <path d="M18 44 L12 38 L7 45" stroke="#fff" stroke-width="3" fill="none"/>
          <text x="35" y="42" text-anchor="middle" font-family="Teko, sans-serif" font-size="22" font-weight="600" fill="#fff">24/7</text>
        </svg>
      </div>
      <p class="feature__label">24/7 EMERGENCY</p>
    </div>
    <div class="feature" style="left:820px; top:520px">
      <div class="feature__circle">
        <svg width="56" height="56" viewBox="0 0 56 56" aria-hidden="true" fill="#fff">
          <path d="M8 6 a12 12 0 0 0 14 16 l26 26 a4 4 0 0 0 6 -6 l-26 -26 a12 12 0 0 0 -16 -14 l7 7 -2 6 -6 2z"/>
          <path d="M40 6 l8 -2 4 4 -2 8 -14 14 -6 -6z"/>
          <path d="M24 36 l-14 14 a3 3 0 0 1 -4 -4 l14 -14z"/>
        </svg>
      </div>
      <p class="feature__label">INSTALLATIONS</p>
    </div>
  </section>

</main>
</body>
</html>
```